business card design for a plumbing contractor

i need a double business card for a plumbing business, our initial service is residential Sewer Drain Cleaning.

Target Market(s)

other plumbing Business

Industry/Entity Type

Plumbing

Contact Information for Business Card

www.PipeworksTopMark.example- 5307218394-

Font styles to use
Serif

Colors
ec1f27
0455a3

```html
<!DOCTYPE html>
<html lang="en">
<head>
<meta charset="utf-8">
<title>Pipeworks Top Mark – Business Card</title>
<link rel="stylesheet" href="https://fonts.googleapis.com/css2?family=Arimo:wght@400;700&display=swap">
<style>
  :root {
    --brand-red: #ec1f27;
    --brand-blue: #0455a3;
    --blue-light: #2f78bd;
    --ink: #1d1d1d;
    --logo-grey: #6b6661;
    --stage: #e9eaec;
    --card-white: #ffffff;
  }
  * { box-sizing: border-box; margin: 0; padding: 0; }
  html, body { width: 1200px; height: 997px; overflow: hidden; }
  body {
    background: var(--stage);
    font-family: "Arimo", Arial, sans-serif;
    display: flex;
    flex-direction: column;
    align-items: center;
    justify-content: center;
    gap: 44px;
  }
  .card {
    position: relative;
    width: 700px;
    height: 400px;
    border-radius: 26px;
    overflow: hidden;
    box-shadow: 0 10px 28px rgba(0,0,0,0.18);
  }

  /* Back side */
  .card--back {
    background: linear-gradient(135deg, var(--blue-light) 0%, var(--brand-blue) 70%);
    color: #fff;
  }
  .service-list {
    position: absolute;
    top: 52px;
    right: 54px;
    list-style: none;
    text-align: right;
    font-size: 22px;
    line-height: 1.9;
    color: rgba(255,255,255,0.88);
  }
  .card--back .wordmark {
    position: absolute;
    left: 56px;
    bottom: 58px;
    color: #fff;
    font-size: 50px;
    font-weight: 700;
    line-height: 0.98;
  }

  /* Front side */
  .card--front { background: var(--card-white); }
  .card--front .wordmark {
    position: absolute;
    top: 40px;
    right: 54px;
    text-align: right;
    color: var(--logo-grey);
    font-size: 44px;
    font-weight: 700;
    line-height: 0.98;
  }
  .holder {
    position: absolute;
    top: 72px;
    left: 56px;
  }
  .holder__name {
    color: var(--brand-red);
    font-size: 26px;
    font-weight: 700;
    letter-spacing: 0.5px;
  }
  .holder__role {
    color: var(--brand-blue);
    font-size: 20px;
    margin-top: 2px;
  }
  .icon-tab {
    position: absolute;
    left: 0;
    top: 236px;
    width: 46px;
    height: 108px;
    background: var(--brand-blue);
    border-radius: 0 12px 12px 0;
    display: flex;
    flex-direction: column;
    align-items: center;
    justify-content: space-evenly;
  }
  .contact-list {
    position: absolute;
    left: 72px;
    top: 238px;
    list-style: none;
    font-size: 21px;
    line-height: 35px;
    color: var(--ink);
  }
  .footer-band {
    position: absolute;
    left: 0;
    bottom: 0;
    width: 100%;
    height: 56px;
  }
</style>
</head>
<body>

  <section class="card card--back" aria-label="Card back">
    <ul class="service-list">
      <li>Sewer Drain Cleaning</li>
      <li>Maintenance</li>
      <li>Trenchless Pipe Installs</li>
    </ul>
    <div class="wordmark">Pipeworks<br>Top Mark</div>
  </section>

  <section class="card card--front" aria-label="Card front">
    <div class="wordmark">Pipeworks<br>Top Mark</div>

    <div class="holder">
      <p class="holder__name">MARCO VELLANI</p>
      <p class="holder__role">Director</p>
    </div>

    <div class="icon-tab" aria-hidden="true">
      <svg width="14" height="20" viewBox="0 0 14 20"><rect x="1.5" y="1" width="11" height="18" rx="2" fill="none" stroke="#fff" stroke-width="2"/><circle cx="7" cy="15.5" r="1.2" fill="#fff"/></svg>
      <svg width="18" height="13" viewBox="0 0 18 13"><rect x="1" y="1" width="16" height="11" rx="1.5" fill="#fff"/><path d="M1.5 1.5 L9 7.5 L16.5 1.5" fill="none" stroke="#0455a3" stroke-width="1.6"/></svg>
      <svg width="14" height="19" viewBox="0 0 14 19"><path d="M7 1 C3.4 1 1 3.6 1 6.8 C1 11 7 18 7 18 C7 18 13 11 13 6.8 C13 3.6 10.6 1 7 1 Z" fill="#fff"/><circle cx="7" cy="6.8" r="2.3" fill="#0455a3"/></svg>
    </div>

    <ul class="contact-list">
      <li>5307218394</li>
      <li>dispatch@PipeworksTopMark.example</li>
      <li>www.PipeworksTopMark.example</li>
    </ul>

    <svg class="footer-band" viewBox="0 0 700 56" preserveAspectRatio="none" aria-hidden="true">
      <path d="M0 36 L500 36 Q540 36 556 10 L556 56 L0 56 Z" fill="var(--brand-red)"/>
      <path d="M540 56 Q560 6 610 6 L700 6 L700 56 Z" fill="var(--brand-blue)"/>
    </svg>
  </section>

</body>
</html>
```